Varnel Corporate Website for technological company

We need a modern website to promote our product and services.
You can found the actually website at the address: www.varnel-example.ch

We are a new company for B2B market. We would like do show our high precision and innovation capability.

we need a section were is possible to easily upload "news" and documents for our customers.

Target Market(s)

B2B services in the industry market

Industry/Entity Type

It Company

Coding

Coded - Design and coding required

Number of Pages Required

5+ page

Font styles to use
Other font styles liked:
• We accept propositions

Requirements
Must have
• Easy to maintain
• Presentation of the Varnel company
• Presentation of Varnel services and products
• The customer can download our ducumentation
Nice to have
• Sexy and modern

```html
<!DOCTYPE html>
<html lang="en">
<head>
<meta charset="utf-8">
<title>Varnel Sagl – Control Systems</title>
<link href="https://fonts.googleapis.com/css2?family=Open+Sans:wght@400;600;700;800&display=swap" rel="stylesheet">
<style>
:root{
  --gold:#b3a266;
  --gold-dark:#9a8a52;
  --ink:#2a2a2a;
  --dark:#2e2e2e;
  --darker:#232323;
  --text:#5a5a5a;
  --light:#f2f2f2;
  --white:#ffffff;
  --line:#dcdcdc;
}
*{box-sizing:border-box;margin:0;padding:0}
html,body{width:1200px;height:2596px;overflow:hidden}
body{font-family:"Open Sans",Arial,sans-serif;color:var(--text);background:var(--white);position:relative;font-size:14px;line-height:1.55}
.btn{display:inline-block;background:var(--gold);color:var(--white);font-weight:700;font-size:13px;letter-spacing:.5px;padding:12px 26px;text-transform:uppercase}
.btn-light{background:var(--white);color:var(--ink)}

/* hero */
.hero{position:absolute;left:0;top:0;width:1200px;height:880px;
  background:linear-gradient(160deg,#8f8f8f 0%,#6a6a6a 35%,#4a4a4a 65%,#7a7a7a 100%);
  clip-path:polygon(0 0,100% 0,100% 93%,50% 100%,0 93%)}
.topbar{position:absolute;top:0;right:40px;height:36px;display:flex;gap:24px;align-items:center;color:#eee;font-size:12px;z-index:3}
.topbar .flag{width:18px;height:11px;background:#c9c9c9;display:inline-block}
.nav-wrap{position:absolute;top:44px;left:40px;right:40px;height:84px;display:flex;justify-content:space-between;align-items:center;z-index:3}
.brand{display:flex;align-items:center;gap:12px;color:var(--white);font-weight:800;font-size:40px;letter-spacing:1px;line-height:1}
.brand .mark{width:34px;height:34px;background:var(--gold)}
.nav{display:flex;background:rgba(255,255,255,.92);padding:10px 14px;gap:6px}
.nav a{font-size:13px;font-weight:700;color:var(--ink);padding:10px 16px;text-decoration:none;text-transform:uppercase}
.nav a.active{background:var(--gold);color:var(--white)}
.hero-copy{position:absolute;top:280px;left:0;width:1200px;text-align:center;z-index:3;color:var(--white)}
.hero-copy h1{font-size:66px;font-weight:800;letter-spacing:1px;line-height:1.1}
.hero-copy p{font-size:19px;margin:22px auto 0;width:760px;line-height:1.5}
.hero-copy .btn{margin-top:34px;font-size:15px;padding:14px 30px}
.dots{position:absolute;top:750px;left:0;width:1200px;display:flex;justify-content:center;gap:10px;z-index:3}
.dots span{width:18px;height:18px;border-radius:50%;border:2px solid var(--white)}
.dots span.on{background:var(--gold);border-color:var(--gold)}

/* welcome */
.welcome{position:absolute;top:890px;left:72px;width:690px}
h2.title{font-size:28px;font-weight:800;color:var(--ink);text-transform:uppercase;padding-bottom:12px;border-bottom:3px solid var(--gold);display:inline-block;margin-bottom:18px;line-height:1.3}
.welcome p{margin-bottom:12px}
.welcome .lead{color:var(--gold-dark);font-weight:700}
.ticks{list-style:none;margin:4px 0 20px}
.ticks li{display:flex;gap:10px;align-items:center;margin-bottom:4px}
.ticks svg{flex:none}

/* sidebar */
.side{position:absolute;top:772px;left:800px;width:340px;z-index:4}
.download{background:var(--dark);color:var(--white);display:flex;align-items:center;gap:14px;padding:18px 22px;font-weight:800;font-size:18px;line-height:1.2;text-transform:uppercase}
.news{background:var(--light);padding:22px 24px 28px;margin-top:14px}
.news h3{font-size:24px;font-weight:800;color:var(--ink);text-transform:uppercase;margin-bottom:14px}
.news .item{margin-bottom:16px}
.news .date{color:var(--gold-dark);font-weight:700;font-size:13px}
.news p{font-size:14px;line-height:1.5}

/* services */
.services{position:absolute;top:1390px;left:0;width:1200px;height:510px;background:var(--dark);color:#cfcfcf;text-align:center;
  clip-path:polygon(0 5%,50% 0,100% 5%,100% 100%,0 100%)}
.services h2{color:var(--white);font-size:34px;font-weight:800;margin-top:50px;line-height:1.3}
.services .rule{width:70px;height:3px;background:var(--gold);margin:14px auto 0}
.svc-grid{display:flex;justify-content:center;gap:40px;margin-top:36px}
.svc{width:230px}
.svc h4{color:var(--gold);font-size:17px;font-weight:800;margin:16px 0 8px;text-transform:uppercase}
.svc p{font-size:13px;line-height:1.55}
.services .btn{margin-top:36px}

/* products */
.products{position:absolute;top:1935px;left:72px;width:1056px;height:400px}
.tabs{position:absolute;top:100px;left:0;width:230px}
.tabs div{padding:12px 16px;font-size:13px;font-weight:700;text-transform:uppercase;border:1px solid var(--line);color:var(--ink)}
.tabs div.on{background:var(--gold);color:var(--white);border-color:var(--gold)}
.prod-thumb{position:absolute;top:100px;left:250px;width:220px;height:200px;background:linear-gradient(135deg,#e8e8e8,#bdbdbd)}
.prod-text{position:absolute;top:92px;left:490px;width:300px}
.prod-text h4{font-size:20px;font-weight:800;color:var(--ink);line-height:1.2}
.prod-text h5{font-size:12px;font-weight:700;color:var(--ink);text-transform:uppercase;margin-bottom:12px}
.prod-text p{font-size:13px;line-height:1.55}
.prod-photo{position:absolute;top:92px;left:810px;width:246px;height:230px;background:radial-gradient(circle at 50% 45%,#3f7a4e,#274e33 60%,#e9e9e9 61%)}
.products .btn{position:absolute;top:320px;left:250px}

/* footer */
.footer{position:absolute;top:2360px;left:0;width:1200px;height:192px;background:var(--darker);color:#bdbdbd;font-size:13px}
.footer .brand{position:absolute;top:50px;left:56px;font-size:34px}
.fcol{position:absolute;top:26px}
.fcol h4{color:var(--white);font-size:17px;font-weight:800;text-transform:uppercase;margin-bottom:10px}
.fcol .row{line-height:1.7}
.field{width:220px;height:30px;background:var(--white);margin-top:8px}
.fcol .btn{padding:7px 14px;font-size:11px;margin-top:8px}
.socials{display:flex;gap:8px;margin-top:12px}
.socials span{width:30px;height:30px;border-radius:50%;border:2px solid #cfcfcf}
.copy{position:absolute;top:2552px;left:0;width:1200px;height:44px;background:#1a1a1a;color:#9a9a9a;font-size:12px;text-align:center;line-height:44px}
</style>
</head>
<body>

<section class="hero" role="img" aria-label="Photo of engineers working in a bright modern office"></section>
<div class="topbar"><span>+41 (0)00 555 0142</span><span>info@varnel-example.ch</span><span>ITALIANO / LOG IN</span><span class="flag"></span></div>
<header class="nav-wrap">
  <div class="brand"><span class="mark"></span>Varnel Sagl</div>
  <nav class="nav">
    <a class="active">Home</a><a>Services</a><a>Products</a><a>Examples</a><a>Downloads</a><a>Contacts</a>
  </nav>
</header>
<div class="hero-copy">
  <h1>VARNEL CONTROL SYSTEMS</h1>
  <p>VARNEL Ltd. designs systems in which electronics, software and mechanics are perfectly integrated to achieve uncompromising performance</p>
  <span class="btn btn-light">Read More</span>
</div>
<div class="dots"><span class="on"></span><span></span><span></span><span></span><span></span></div>

<section class="welcome">
  <h2 class="title">Welcome to our website</h2>
  <p>The ever-increasing complexity in modern systems, the search for reliability and performance and the continuous desire to reduce production costs and dimensions of the products require a rigorous integration between the electronic units, software and mechanical design.</p>
  <p>VARNEL Ltd. designs systems in which electronics, software and mechanics are perfectly integrated to achieve uncompromising performance.</p>
  <p>VARNEL Ltd. designs systems in which electronics, software and mechanics are perfectly integrated to achieve uncompromising performance.</p>
  <p class="lead">VARNEL Ltd. is a company active in the following areas:</p>
  <ul class="ticks">
    <li><svg width="16" height="16" viewBox="0 0 16 16"><circle cx="8" cy="8" r="8" fill="#b3a266"/><path d="M4 8l3 3 5-6" stroke="#fff" stroke-width="2" fill="none"/></svg>Simulation and modeling of complete processes</li>
    <li><svg width="16" height="16" viewBox="0 0 16 16"><circle cx="8" cy="8" r="8" fill="#b3a266"/><path d="M4 8l3 3 5-6" stroke="#fff" stroke-width="2" fill="none"/></svg>Concept and design of electronic circuits and mechanical units</li>
    <li><svg width="16" height="16" viewBox="0 0 16 16"><circle cx="8" cy="8" r="8" fill="#b3a266"/><path d="M4 8l3 3 5-6" stroke="#fff" stroke-width="2" fill="none"/></svg>Development of application specific control software</li>
    <li><svg width="16" height="16" viewBox="0 0 16 16"><circle cx="8" cy="8" r="8" fill="#b3a266"/><path d="M4 8l3 3 5-6" stroke="#fff" stroke-width="2" fill="none"/></svg>Rapid prototyping (electronic cards, mechanisms ...)</li>
  </ul>
  <span class="btn">Read More</span>
</section>

<aside class="side">
  <div class="download">
    <svg width="40" height="40" viewBox="0 0 40 40"><path d="M20 6v20M12 18l8 8 8-8M8 32h24" stroke="#fff" stroke-width="3" fill="none"/></svg>
    <span>Download<br>Brochure Varnel<small style="font-size:12px;font-weight:600"> (pdf)</small></span>
  </div>
  <div class="news">
    <h3>Latest News</h3>
    <div class="item"><div class="date">OCT 18, 2016</div><p>The Varnel team will be present at the stand A16 of Techfair exhibition in Bern, between 6 and 8 September 2016.</p></div>
    <div class="item"><div class="date">OCT 11, 2016</div><p>Added the 'application' page, showing some of the developments of Varnel Ltd.</p></div>
    <span class="btn">Read All News</span>
  </div>
</aside>

<section class="services">
  <h2>OUR SERVICES</h2>
  <div class="rule"></div>
  <div class="svc-grid">
    <div class="svc">
      <svg width="64" height="64" viewBox="0 0 64 64" fill="none" stroke="#fff" stroke-width="3"><rect x="16" y="16" width="32" height="32"/><rect x="25" y="25" width="14" height="14"/><path d="M24 8v8M32 8v8M40 8v8M24 48v8M32 48v8M40 48v8M8 24h8M8 32h8M8 40h8M48 24h8M48 32h8M48 40h8"/></svg>
      <h4>Electronics</h4>
      <p>Varnel Sagl being active in all fields associated with actuator electronics, can develop solutions integrating...</p>
    </div>
    <div class="svc">
      <svg width="64" height="64" viewBox="0 0 64 64" fill="none" stroke="#fff" stroke-width="3"><circle cx="26" cy="28" r="12"/><circle cx="26" cy="28" r="4"/><circle cx="46" cy="44" r="8"/><circle cx="46" cy="44" r="3"/><path d="M26 10v6M26 40v6M8 28h6M38 28h6M46 30v6M46 52v4"/></svg>
      <h4>Mechanics</h4>
      <p>Varnel Sagl being active in all fields associated with actuator electronics, can develop solutions integrating...</p>
    </div>
    <div class="svc">
      <svg width="64" height="64" viewBox="0 0 64 64" fill="none" stroke="#fff" stroke-width="3"><rect x="14" y="14" width="36" height="26"/><path d="M6 48h52l-4-8H10z"/></svg>
      <h4>Software</h4>
      <p>Varnel Sagl being active in all fields associated with actuator electronics, can develop solutions integrating...</p>
    </div>
    <div class="svc">
      <svg width="64" height="64" viewBox="0 0 64 64" fill="none" stroke="#fff" stroke-width="3"><rect x="8" y="10" width="48" height="36"/><path d="M32 18l10 6v12l-10 6-10-6V24zM22 24l10 6 10-6M32 30v12M24 54h16M32 46v8"/></svg>
      <h4>Simulation &amp; Modeling</h4>
      <p>Varnel Sagl being active in all fields associated with actuator electronics, can develop solutions integrating...</p>
    </div>
  </div>
  <span class="btn">View All Services</span>
</section>

<section class="products">
  <h2 class="title">Our Products</h2>
  <div class="tabs"><div>Motor Driver</div><div class="on">Bus Interface</div></div>
  <div class="prod-thumb" role="img" aria-label="Product image of the motor driver board"></div>
  <div class="prod-text">
    <h4>PETREL:</h4>
    <h5>Intelligent control for electric motors</h5>
    <p>Petrel is an electronic board developed for the control of DC and BLDC motors with a power ranging from 1W to 250W. The board integrates a powerful ARM processor, a power stage, two communication buses, a number of interfaces compatible with the different position sensor standards available on the market...</p>
  </div>
  <div class="prod-photo" role="img" aria-label="Photo of the green Petrel controller circuit board"></div>
  <span class="btn">View All Product</span>
</section>

<footer class="footer">
  <div class="brand"><span class="mark"></span>Varnel Sagl</div>
  <div class="fcol" style="left:400px">
    <h4>Contact Us</h4>
    <div class="row">☏ +41 (0)00 555 0142 (Phone)</div>
    <div class="row">☏ +41 (0)00 555 0143 (Fax)</div>
    <div class="row">✉ info@varnel-example.ch</div>
    <div class="row">⌂ Strada Esempio 14, 6999 Borgonuovo</div>
  </div>
  <div class="fcol" style="left:640px">
    <h4>Newsletter</h4>
    <div style="width:230px;line-height:1.4">Register your email address to get information about us</div>
    <div class="field"></div>
    <span class="btn">Subscribe</span>
  </div>
  <div class="fcol" style="left:920px">
    <h4>Follow Us</h4>
    <div style="width:220px;line-height:1.4">Stay up to date with our latest news, events and product releases online.</div>
    <div class="socials"><span></span><span></span><span></span><span></span><span></span></div>
  </div>
</footer>
<div class="copy">Copyright © Varnel · All rights reserved</div>

</body>
</html>
```